Brisk Fixwell business card

I need business card for my business, I think you have all my details.six months ago I design with you car wrap design. We would like to design both side of the card. On front of card we would like logo , Name and our contact details.
At the back we are looking to mentioned our services.
The name will be:
Faridoullan Mestor
Managing Director
Ph:07952338417
Email:info@brisk-fixwell.com
Web:www.brisk-fixwell.com
So we have our logo, you don’t need to change the logo.
Please see the attachment.
Thanks

Target Market(s)

Home improvement

Industry/Entity Type

Home Improvement

Contact Information for Business Card

Company name: Brisk Fixwell
Name: Faridoullan Mestor
Position: Director
Ph:07952338417
Web: www.brisk-fixwell.com
Add: 42 Corvale Road
Hounslow
TW3 9KD
SECOND PERSON
Nizamuddel mestor
Position: Handyman
Ph: 07812 564037
Email: info@brisk-fixwell.com
Add: 18 Brackwin Lane Road
Hounslow
TW6 2LB

```html
<!DOCTYPE html>
<html lang="en">
<head>
<meta charset="utf-8">
<title>Brisk Fixwell business card</title>
<link rel="stylesheet" href="https://fonts.googleapis.com/css2?family=Arimo:wght@400;700&display=swap">
<style>
  :root {
    --stage: #1f1f21;
    --navy: #253a80;
    --red: #e31e2d;
    --white: #ffffff;
    --ink: #3a3a3c;
    --grey: #6b6b6e;
    --rule: #d9d9dc;
  }
  * { box-sizing: border-box; margin: 0; padding: 0; }
  html, body { width: 1200px; height: 1015px; overflow: hidden; }
  body {
    background: var(--stage);
    font-family: "Arimo", Arial, sans-serif;
    display: flex;
    flex-direction: column;
    align-items: center;
    justify-content: center;
    gap: 56px;
  }
  .card {
    position: relative;
    width: 760px;
    height: 434px;
    overflow: hidden;
    box-shadow: 0 14px 30px rgba(0,0,0,.55);
  }

  /* Services side */
  .card--services { background: var(--navy); }
  .card--services .red-field {
    position: absolute; inset: 0; width: 100%; height: 100%;
  }
  .service-list {
    position: absolute;
    left: 392px;
    top: 78px;
    list-style: none;
    color: var(--white);
    font-size: 17px;
    letter-spacing: .5px;
    line-height: 29px;
  }
  .service-list li { display: flex; align-items: center; gap: 12px; }
  .service-list svg { width: 14px; height: 12px; flex: none; }

  /* Contact side */
  .card--contact { background: var(--white); }
  .brand {
    position: absolute;
    left: 70px;
    top: 188px;
    display: flex;
    align-items: center;
    gap: 12px;
    color: var(--navy);
    font-weight: 700;
    font-size: 34px;
    letter-spacing: .5px;
  }
  .brand-square { width: 22px; height: 22px; background: var(--navy); }
  .divider {
    position: absolute;
    left: 370px; top: 40px;
    width: 1px; height: 300px;
    background: var(--rule);
  }
  .contact {
    position: absolute;
    left: 402px;
    top: 78px;
    color: var(--ink);
  }
  .contact-name {
    color: var(--navy);
    font-weight: 700;
    font-size: 22px;
    letter-spacing: .5px;
    text-transform: uppercase;
  }
  .contact-role {
    color: var(--grey);
    font-size: 16px;
    letter-spacing: .8px;
    margin-top: 2px;
  }
  .contact-lines { list-style: none; margin-top: 18px; font-size: 17px; line-height: 28px; }
  .contact-lines li { display: flex; align-items: center; gap: 10px; }
  .contact-lines svg { width: 16px; height: 16px; flex: none; fill: var(--navy); }
  .contact-lines .web-domain { color: var(--navy); }
  .contact-address { margin-top: 14px; font-size: 17px; line-height: 24px; font-style: normal; }
  .band-red {
    position: absolute; left: 0; bottom: 0;
    width: 468px; height: 18px; background: var(--red);
  }
  .band-navy {
    position: absolute; right: 0; bottom: 0;
    width: 286px; height: 44px; background: var(--navy);
  }
</style>
</head>
<body>

<section class="card card--services" aria-label="Services">
  <svg class="red-field" viewBox="0 0 760 434" preserveAspectRatio="none" aria-hidden="true">
    <path d="M0 150 L0 434 L300 434 Q360 340 352 240 Q340 160 300 110 Z" fill="var(--red)"/>
  </svg>
  <ul class="service-list">
    <li><svg viewBox="0 0 14 12"><path d="M7 0 L14 7 H10 V12 H4 V7 H0 Z" fill="var(--red)"/></svg>PLUMBING</li>
    <li><svg viewBox="0 0 14 12"><path d="M7 0 L14 7 H10 V12 H4 V7 H0 Z" fill="var(--red)"/></svg>CARPENTRY</li>
    <li><svg viewBox="0 0 14 12"><path d="M7 0 L14 7 H10 V12 H4 V7 H0 Z" fill="var(--red)"/></svg>PAINTING &amp; DECORATING</li>
    <li><svg viewBox="0 0 14 12"><path d="M7 0 L14 7 H10 V12 H4 V7 H0 Z" fill="var(--red)"/></svg>DECKING</li>
    <li><svg viewBox="0 0 14 12"><path d="M7 0 L14 7 H10 V12 H4 V7 H0 Z" fill="var(--red)"/></svg>FENCE</li>
    <li><svg viewBox="0 0 14 12"><path d="M7 0 L14 7 H10 V12 H4 V7 H0 Z" fill="var(--red)"/></svg>GUTTER</li>
    <li><svg viewBox="0 0 14 12"><path d="M7 0 L14 7 H10 V12 H4 V7 H0 Z" fill="var(--red)"/></svg>FLOORING</li>
    <li><svg viewBox="0 0 14 12"><path d="M7 0 L14 7 H10 V12 H4 V7 H0 Z" fill="var(--red)"/></svg>PLASTERING</li>
    <li><svg viewBox="0 0 14 12"><path d="M7 0 L14 7 H10 V12 H4 V7 H0 Z" fill="var(--red)"/></svg>TILLING</li>
    <li><svg viewBox="0 0 14 12"><path d="M7 0 L14 7 H10 V12 H4 V7 H0 Z" fill="var(--red)"/></svg>GARDENING</li>
  </ul>
</section>

<section class="card card--contact" aria-label="Contact details">
  <div class="brand"><span>Brisk Fixwell</span><span class="brand-square" aria-hidden="true"></span></div>
  <div class="divider" aria-hidden="true"></div>
  <div class="contact">
    <h1 class="contact-name">Faridoullan Mestor</h1>
    <p class="contact-role">DIRECTOR</p>
    <ul class="contact-lines">
      <li><svg viewBox="0 0 16 16" aria-hidden="true"><path d="M3 1 L6 1 L7 5 L5 6.5 Q6.5 9.5 9.5 11 L11 9 L15 10 L15 13 Q15 15 13 15 Q2 14 1 3 Q1 1 3 1 Z"/></svg>07952338417</li>
      <li><svg viewBox="0 0 16 16" aria-hidden="true"><path d="M0 3 H16 V13 H0 Z M1 4 L8 9 L15 4 Z" fill-rule="evenodd"/></svg>info@brisk-fixwell.com</li>
      <li><svg viewBox="0 0 16 16" aria-hidden="true"><path d="M8 0 A8 8 0 1 0 8 16 A8 8 0 1 0 8 0 Z M8 1.5 A6.5 6.5 0 1 1 8 14.5 A6.5 6.5 0 1 1 8 1.5 Z M7.3 1.5 H8.7 V14.5 H7.3 Z M1.5 7.3 H14.5 V8.7 H1.5 Z M8 1.5 Q4 8 8 14.5 L8 13 Q5.5 8 8 3 Z M8 1.5 Q12 8 8 14.5 L8 13 Q10.5 8 8 3 Z" fill-rule="evenodd"/></svg><span>www.<span class="web-domain">brisk-fixwell</span>.com</span></li>
    </ul>
    <address class="contact-address">42 Corvale Road<br>Hounslow, TW3 9KD</address>
  </div>
  <div class="band-red" aria-hidden="true"></div>
  <div class="band-navy" aria-hidden="true"></div>
</section>

</body>
</html>
```